BRIGHTHOLD PROPERTY MANAGEMENT INC. WEBSITE

Please make the website more family-friendly.

I want a website to help me build my property management business by adding listing properties and creating an online application. Im open to any other ideas.
I want a WordPress designer to code it.

Here is my current website. www.brighthold.biz

IDEA: I like the website design https://www.pelicanclimateservices.com/

Thank you

Tom

Number of Pages Required

5+ page

```html
<!DOCTYPE html>
<html lang="en">
<head>
<meta charset="utf-8">
<title>Brighthold Property Management</title>
<link href="https://fonts.googleapis.com/css2?family=Cinzel:wght@400;600&family=Roboto:wght@400;500;700&display=swap" rel="stylesheet">
<style>
:root{
  --red:#a5121b;
  --red-dark:#7d0b11;
  --red-bright:#c8161e;
  --pink:#f8c4c4;
  --pink-soft:#fbe9e8;
  --soft:#f5f3f2;
  --ink:#1b1b1b;
  --text:#6b6b6b;
  --line:#3a3a3a;
  --green:#2e9b3a;
}
*{box-sizing:border-box;margin:0;padding:0}
html,body{width:1200px;height:4037px;overflow:hidden}
body{position:relative;font-family:"Roboto",Arial,sans-serif;color:var(--ink);background:#fff}
.abs{position:absolute}
.serif{font-family:"Cinzel","Times New Roman",serif}

/* top bar + nav */
.topbar{left:0;top:0;width:1200px;height:31px;background:var(--red);color:#fff;font-size:14px}
.topbar .social{left:110px;top:4px;display:flex;gap:5px}
.topbar .social span{width:23px;height:23px;border-radius:50%;background:#fff;display:block}
.topbar .item{top:7px}
.nav{left:0;top:31px;width:1200px;height:53px;background:#fff;border-bottom:1px solid #ddd}
.nav a{position:absolute;top:18px;font-size:14px;font-weight:500;color:var(--ink);text-decoration:none}
.nav .sep{position:absolute;top:0;width:1px;height:53px;background:#ddd}
.logo-tab{left:540px;top:0;width:118px;height:96px;background:#fff;clip-path:polygon(0 0,100% 0,100% 86%,50% 100%,0 86%)}
.logo-tab span{position:absolute;left:0;width:118px;top:46px;text-align:center;font-family:"Cinzel",serif;font-size:14px;color:var(--red)}
.logo-tab i{position:absolute;left:49px;top:14px;width:20px;height:20px;border:2px solid var(--red)}

/* hero */
.hero-band{left:0;top:84px;width:1200px;height:660px;background:var(--red);clip-path:polygon(0 80%,50% 100%,100% 80%,100% 84%,50% 100%,0 84%)}
.hero{left:0;top:84px;width:1200px;height:645px;background:linear-gradient(180deg,#c3151d 0%,#8e1a1c 38%,#3d3436 70%,#5b4a3c 100%);clip-path:polygon(0 0,100% 0,100% 80%,50% 100%,0 80%)}
.hero-text{left:0;width:1200px;text-align:center;color:#fff}
.btn{position:absolute;display:flex;align-items:center;justify-content:center;gap:10px;background:var(--red);color:#fff;font-size:14px;font-weight:700;border-radius:6px;text-transform:uppercase}
.btn i{width:15px;height:13px;border:2px solid #fff;border-radius:2px;display:block}

/* headings */
.h-sec{font-family:"Cinzel",serif;font-size:44px;font-weight:400;letter-spacing:1px;color:var(--ink)}
.h-sec em{font-style:normal;color:var(--red)}
.h-center{left:0;width:1200px;display:flex;justify-content:center;align-items:center;gap:12px}
.h-center.light{color:#fff}
.body-text{font-size:13.5px;line-height:26px;color:var(--text)}

/* about */
.about-frame{left:128px;top:791px;width:306px;height:301px;border:2px solid var(--red)}
.about-photo{left:163px;top:821px;width:367px;height:362px;background:linear-gradient(160deg,#f1efed,#cfc6bd 60%,#8a7d72)}

/* services */
.services{left:0;top:1288px;width:1200px;height:553px;background:linear-gradient(90deg,#f7f2f1,#f3f3f3)}
.svc-label{font-size:16px;font-weight:700;color:var(--ink)}
.svc-circle{width:70px;height:70px;border-radius:50%;border:2px solid var(--line);background:#fff}

/* listings */
.listing-band{left:0;top:1841px;width:1200px;height:404px;background:linear-gradient(90deg,#a31218,#b8161e 50%,#a31218)}
.card{width:294px;height:411px;top:2007px;background:#fff;border-radius:8px;box-shadow:0 4px 14px rgba(0,0,0,.22);padding:6px}
.card .photo{width:282px;height:196px;border-radius:6px}
.card h3{margin:24px 0 0 20px;font-size:17px;font-weight:500}
.card .addr{margin:12px 0 0 20px;font-size:13px;color:var(--text)}
.card .status{margin:12px 0 0 20px;font-size:13px}
.card .status b{font-weight:500;color:var(--red)}
.card .status span{color:var(--green)}
.card .meta{margin:16px 0 0 24px;font-size:13px;color:var(--text);display:flex;align-items:center;gap:8px}
.card .meta b{font-weight:500;color:var(--red)}
.card .meta i{width:14px;height:14px;border:1.5px solid var(--red);display:block}
.card .more{margin:22px 0 0 1px;width:280px;height:44px;background:var(--red);border-radius:6px;color:#fff;font-size:14px;font-weight:700;display:flex;align-items:center;justify-content:center}
.arrow{width:34px;height:34px;border-radius:50%;background:#fff;top:2164px}

/* property management */
.pm-photo{left:642px;top:2504px;width:377px;height:481px;background:linear-gradient(180deg,#ffffff 0%,#d8c2ad 40%,#a8774f 75%,#8c8c8c 100%);border-radius:190px 190px 0 0}
.tag{display:flex;align-items:center;justify-content:center;text-align:center;font-family:"Cinzel",serif;font-size:14px;line-height:28px;border-radius:6px}

/* contact */
.contact{left:0;top:2985px;width:1200px;height:666px;background:linear-gradient(180deg,#fff,#f5f3f3)}
.contact-photo{left:119px;top:3142px;width:384px;height:388px;background:linear-gradient(150deg,#3b3f47,#9a9aa0 50%,#e7e4e2)}
.contact-frame{left:743px;top:3171px;width:326px;height:308px;border:2px solid var(--red)}
.form-card{left:439px;top:3189px;width:605px;height:412px;background:#fff;box-shadow:0 4px 18px rgba(0,0,0,.15)}
.form-card h2{position:absolute;left:50px;top:30px;font-family:"Cinzel",serif;font-weight:400;font-size:38px;letter-spacing:2px}
.form-card h2 em{font-style:normal;color:var(--red)}
.field{position:absolute;width:240px}
.field label{display:block;font-size:14px;font-weight:500}
.field div{margin-top:10px;font-size:12px;color:var(--text);padding-bottom:8px;border-bottom:1px solid #999}
.send{left:514px;top:322px;width:46px;height:46px;border-radius:50%;background:var(--red)}

/* footer */
.footer-links{left:0;width:1200px;top:3874px;display:flex;justify-content:center;gap:38px;color:#fff;font-size:16px;font-weight:500}
.copy{left:0;width:1200px;top:3930px;text-align:center;color:#fff;font-size:13px}
.f-social{left:496px;top:3972px;display:flex;gap:11px}
.f-social span{width:33px;height:33px;background:var(--red);border-radius:3px;display:block}
</style>
</head>
<body>

<!-- top bar -->
<div class="abs topbar">
  <div class="abs social"><span></span><span></span><span></span><span></span></div>
  <div class="abs item" style="left:270px">&#9742; (555) 014-2290</div>
  <div class="abs item" style="left:832px">&#9679; Login</div>
  <div class="abs item" style="left:934px">&#9993; info@brighthold.biz</div>
</div>
<nav class="abs nav">
  <a style="left:112px">Listings</a><span class="sep" style="left:193px"></span>
  <a style="left:239px">Owners</a><span class="sep" style="left:326px"></span>
  <a style="left:367px">Prospect Tenants</a>
  <a style="left:714px">About</a><span class="sep" style="left:790px"></span>
  <a style="left:822px">Community</a><span class="sep" style="left:928px"></span>
  <a style="left:968px">Mortgage Info</a>
</nav>
<div class="abs logo-tab"><i></i><span>BRIGHTHOLD</span></div>

<!-- hero -->
<div class="abs hero-band"></div>
<div class="abs hero" role="img" aria-label="Modern two-storey house with lit garage doors at dusk under a red sky"></div>
<div class="abs hero-text" style="top:344px;font-size:16px;font-weight:500">WELCOME TO</div>
<div class="abs hero-text serif" style="top:372px;font-size:62px;letter-spacing:2px">BRIGHTHOLD</div>
<div class="abs hero-text" style="top:464px;font-size:17px;font-weight:700;line-height:29px">EXPERT MANAGEMENT FOR EXCEPTIONAL<br>PROPERTIES</div>
<div class="btn" style="left:522px;top:540px;width:156px;height:43px">Contact us <i></i></div>

<!-- about -->
<div class="abs about-frame"></div>
<div class="abs about-photo" role="img" aria-label="Happy family walking into the bright hallway of their new home"></div>
<div class="abs h-sec" style="left:658px;top:830px;display:flex;align-items:center;gap:14px">About <em>us</em>
  <svg width="40" height="24" viewBox="0 0 40 24"><g stroke="#1b1b1b" stroke-width="2"><line x1="0" y1="2" x2="40" y2="2"/><line x1="0" y1="7" x2="34" y2="7"/><line x1="0" y1="12" x2="28" y2="12"/><line x1="0" y1="17" x2="34" y2="17"/><line x1="0" y1="22" x2="40" y2="22"/></g></svg>
</div>
<p class="abs body-text" style="left:658px;top:893px;width:372px">Lorem ipsum dolor sit amet, consectetur adipiscing elit, sed do eiusmod tempor incididunt ut labore et dolore magna aliqua. Ut enim ad minim veniam, quis nostrud exercitation ullamco laboris nisi ut aliquip ex ea commodo consequat. Duis aute irure dolor in reprehenderit in voluptate velit esse cillum dolore eu fugiat nulla pariatur.</p>
<p class="abs body-text" style="left:658px;top:1058px;width:372px">Lorem ipsum dolor sit amet, consectetur adipiscing elit, sed do eiusmod tempor incididunt</p>
<div class="btn" style="left:658px;top:1128px;width:157px;height:44px">Learn more <i></i></div>

<!-- services -->
<div class="abs services"></div>
<div class="abs h-center h-sec" style="top:1354px">
  <svg width="40" height="24"><g stroke="#1b1b1b" stroke-width="2"><line x1="0" y1="2" x2="40" y2="2"/><line x1="6" y1="7" x2="40" y2="7"/><line x1="12" y1="12" x2="40" y2="12"/><line x1="6" y1="17" x2="40" y2="17"/><line x1="0" y1="22" x2="40" y2="22"/></g></svg>
  <span>Our <em>services</em></span>
  <svg width="40" height="24"><g stroke="#1b1b1b" stroke-width="2"><line x1="0" y1="2" x2="40" y2="2"/><line x1="0" y1="7" x2="34" y2="7"/><line x1="0" y1="12" x2="28" y2="12"/><line x1="0" y1="17" x2="34" y2="17"/><line x1="0" y1="22" x2="40" y2="22"/></g></svg>
</div>
<svg class="abs" style="left:0;top:1288px" width="1200" height="553" viewBox="0 1288 1200 553">
  <g fill="none" stroke="#3a3a3a" stroke-width="2">
    <polyline points="400,1473 460,1473 491,1520"/>
    <polyline points="400,1611 447,1611"/>
    <polyline points="400,1750 460,1750 491,1702"/>
    <polyline points="800,1473 740,1473 709,1520"/>
    <polyline points="800,1611 753,1611"/>
    <polyline points="800,1750 740,1750 709,1702"/>
    <circle cx="600" cy="1611" r="154"/>
  </g>
  <circle cx="600" cy="1611" r="130" fill="#f8c4c4"/>
  <g fill="#a5121b"><circle cx="491" cy="1504" r="4"/><circle cx="447" cy="1611" r="4"/><circle cx="491" cy="1718" r="4"/><circle cx="709" cy="1504" r="4"/><circle cx="753" cy="1611" r="4"/><circle cx="709" cy="1718" r="4"/></g>
  <text x="600" y="1620" text-anchor="middle" font-family="Cinzel, serif" font-size="26" fill="#a5121b">BRIGHTHOLD</text>
</svg>
<div class="abs svc-circle" style="left:330px;top:1438px"></div>
<div class="abs svc-circle" style="left:330px;top:1576px"></div>
<div class="abs svc-circle" style="left:330px;top:1715px"></div>
<div class="abs svc-circle" style="left:800px;top:1438px"></div>
<div class="abs svc-circle" style="left:800px;top:1576px"></div>
<div class="abs svc-circle" style="left:800px;top:1715px"></div>
<svg class="abs" style="left:0;top:1288px" width="1200" height="553" viewBox="0 1288 1200 553">
  <g fill="none" stroke="#a5121b" stroke-width="2">
    <path d="M352 1480 l13-10 13 10 v14 h-26z"/>
    <path d="M352 1619 l13-12 13 12 v14 h-26z"/>
    <circle cx="365" cy="1750" r="12"/><path d="M361 1745 h6 a3 3 0 0 1 0 6 h-4 a3 3 0 0 0 0 6 h6"/>
    <rect x="823" y="1460" width="24" height="28" rx="2"/><line x1="828" y1="1468" x2="842" y2="1468"/><line x1="828" y1="1475" x2="842" y2="1475"/>
    <circle cx="829" cy="1605" r="7"/><line x1="834" y1="1610" x2="848" y2="1624"/>
    <path d="M825 1740 h20 l-4 22 h-12z"/><line x1="835" y1="1745" x2="835" y2="1756"/>
  </g>
</svg>
<div class="abs svc-label" style="left:166px;top:1457px">MORTGAGE UTILITY</div>
<div class="abs svc-label" style="left:107px;top:1602px">INSPECTION OF PROPERTY</div>
<div class="abs svc-label" style="left:170px;top:1739px">RENT COLLECTION</div>
<div class="abs svc-label" style="left:882px;top:1458px">ACCOUNTING</div>
<div class="abs svc-label" style="left:880px;top:1603px">LEASING</div>
<div class="abs svc-label" style="left:880px;top:1739px">SECURITY DEPOSIT</div>

<!-- listings -->
<div class="abs listing-band" role="img" aria-label="Faint city skyline and bridge behind a deep red overlay"></div>
<div class="abs h-center h-sec" style="top:1920px;color:#fff">
  <svg width="40" height="24"><g stroke="#fff" stroke-width="2"><line x1="0" y1="2" x2="40" y2="2"/><line x1="6" y1="7" x2="40" y2="7"/><line x1="12" y1="12" x2="40" y2="12"/><line x1="6" y1="17" x2="40" y2="17"/><line x1="0" y1="22" x2="40" y2="22"/></g></svg>
  <span>Our listings</span>
  <svg width="40" height="24"><g stroke="#fff" stroke-width="2"><line x1="0" y1="2" x2="40" y2="2"/><line x1="0" y1="7" x2="34" y2="7"/><line x1="0" y1="12" x2="28" y2="12"/><line x1="0" y1="17" x2="34" y2="17"/><line x1="0" y1="22" x2="40" y2="22"/></g></svg>
</div>
<div class="abs arrow" style="left:47px"><svg width="34" height="34"><path d="M19 12 l-6 5 6 5z" fill="#1b1b1b"/></svg></div>
<div class="abs arrow" style="left:1119px"><svg width="34" height="34"><path d="M15 12 l6 5 -6 5z" fill="#1b1b1b"/></svg></div>

<div class="abs card" style="left:113px">
  <div class="photo" role="img" aria-label="Single-storey rental unit under a large tree" style="background:linear-gradient(180deg,#5a9bd6,#9ec2e0 35%,#6f8b4e 60%,#b49a7d)"></div>
  <h3>2 Bdrm x 1 Bth ADU Unit</h3>
  <div class="addr">Cedar Falls, CA 95010,Linden, US</div>
  <div class="status"><b>Status:</b>&nbsp; <span>Available</span> (For Rent)</div>
  <div class="meta"><i></i>693 Sq. Ft. &nbsp;&nbsp;<b>Type:</b> &nbsp;Residential</div>
  <div class="more">LEARN MORE</div>
</div>
<div class="abs card" style="left:453px">
  <div class="photo" role="img" aria-label="Ranch-style house with tall pine trees" style="background:linear-gradient(180deg,#3f86d1,#8cb8e0 35%,#3f5e32 60%,#8a8478)"></div>
  <h3>2 Bdrm x 1 Bth ADU Unit</h3>
  <div class="addr">Cedar Falls, CA 95010,Linden, US</div>
  <div class="status"><b>Status:</b>&nbsp; <span>Available</span> (For Rent)</div>
  <div class="meta"><i></i>693 Sq. Ft. &nbsp;&nbsp;<b>Type:</b> &nbsp;Residential</div>
  <div class="more">LEARN MORE</div>
</div>
<div class="abs card" style="left:793px">
  <div class="photo" role="img" aria-label="Bright white kitchen interior of the rental unit" style="background:linear-gradient(135deg,#f2f0ee,#d9d4cf 55%,#8f7f74)"></div>
  <h3>2 Bdrm x 1 Bth ADU Unit</h3>
  <div class="addr">Cedar Falls, CA 95010,Linden, US</div>
  <div class="status"><b>Status:</b>&nbsp; <span>Available</span> (For Rent)</div>
  <div class="meta"><i></i>693 Sq. Ft. &nbsp;&nbsp;<b>Type:</b> &nbsp;Residential</div>
  <div class="more">LEARN MORE</div>
</div>

<!-- property management -->
<div class="abs serif" style="left:113px;top:2534px;font-size:40px;line-height:48px;letter-spacing:1px">
  <div style="display:flex;align-items:center;gap:14px">Property
    <svg width="40" height="24"><g stroke="#1b1b1b" stroke-width="2"><line x1="0" y1="2" x2="40" y2="2"/><line x1="0" y1="7" x2="34" y2="7"/><line x1="0" y1="12" x2="28" y2="12"/><line x1="0" y1="17" x2="34" y2="17"/><line x1="0" y1="22" x2="40" y2="22"/></g></svg></div>
  <div style="color:var(--red)">Management</div>
</div>
<p class="abs body-text" style="left:113px;top:2640px;width:370px">Having the right property manager means having an agent who is committed to helping you and making being a home provider hassle free. I believe clear communication, work ethic, time management, staying focused and knowledge goes a long way in my business.</p>
<p class="abs body-text" style="left:113px;top:2792px;width:370px">This commitment level has helped us build a remarkable track record of delivering results</p>
<div class="btn" style="left:113px;top:2870px;width:157px;height:45px">Learn more <i></i></div>
<div class="abs pm-photo" role="img" aria-label="Smiling property manager in a tan jacket holding a laptop"></div>
<div class="abs tag" style="left:564px;top:2595px;width:162px;height:88px;background:var(--pink-soft)">PROPERTY<br>MANAGER</div>
<div class="abs tag" style="left:904px;top:2620px;width:163px;height:89px;background:var(--red);color:#fff">RENTAL OWNERS</div>
<div class="abs tag" style="left:931px;top:2828px;width:161px;height:87px;background:#f1f1f1">VENDORS</div>

<!-- contact -->
<div class="abs contact"></div>
<div class="abs h-center h-sec" style="top:3056px">
  <svg width="40" height="24"><g stroke="#1b1b1b" stroke-width="2"><line x1="0" y1="2" x2="40" y2="2"/><line x1="6" y1="7" x2="40" y2="7"/><line x1="12" y1="12" x2="40" y2="12"/><line x1="6" y1="17" x2="40" y2="17"/><line x1="0" y1="22" x2="40" y2="22"/></g></svg>
  <span>Contact <em>us</em></span>
  <svg width="40" height="24"><g stroke="#1b1b1b" stroke-width="2"><line x1="0" y1="2" x2="40" y2="2"/><line x1="0" y1="7" x2="34" y2="7"/><line x1="0" y1="12" x2="28" y2="12"/><line x1="0" y1="17" x2="34" y2="17"/><line x1="0" y1="22" x2="40" y2="22"/></g></svg>
</div>
<div class="abs contact-photo" role="img" aria-label="Hands holding a tablet above a small model house with a red roof"></div>
<div class="abs contact-frame"></div>
<div class="abs form-card">
  <h2>Get &nbsp;In <em>Touch</em></h2>
  <div class="field" style="left:51px;top:103px"><label>YOUR NAME</label><div>Alex Reed</div></div>
  <div class="field" style="left:318px;top:103px"><label>EMAIL</label><div>alex.reed@mailbox.test</div></div>
  <div class="field" style="left:51px;top:190px"><label>COMPANY</label><div>Oak Company</div></div>
  <div class="field" style="left:318px;top:190px"><label>PHONE</label><div>+1 (555) 010 0000</div></div>
  <div class="field" style="left:51px;top:280px;width:460px"><label>MESSAGE</label><div style="padding-bottom:32px">Hi , Do you have Mpment To Talk About Us</div></div>
  <div class="abs send"><svg width="46" height="46"><path d="M14 24 l18-9 -7 18 -3-7z" fill="#fff"/></svg></div>
</div>

<!-- footer -->
<svg class="abs" style="left:0;top:3651px" width="1200" height="386" viewBox="0 0 1200 386">
  <polygon points="0,96 600,0 1200,96 1200,110 600,12 0,110" fill="#a5121b"/>
  <polygon points="0,110 600,26 1200,110 1200,386 0,386" fill="#000"/>
</svg>
<div class="abs serif" style="left:0;width:1200px;top:3768px;text-align:center;color:#fff;font-size:30px;letter-spacing:2px">BRIGHTHOLD</div>
<div class="abs footer-links"><span>LISTINGS</span><span>OWNERS</span><span>PROSPECT TENANTS</span><span>ABOUT</span><span>COMMUNITY MORTGAGE INFO</span></div>
<div class="abs copy">Copyright© 2024 BRIGHTHOLD PROPERTY MANAGEMENT INC.</div>
<div class="abs f-social"><span></span><span></span><span></span><span></span><span></span></div>

</body>
</html>
```